Letterhead Design Project

Based on the attached logo we would like have a designed of stationary.
As we are a management consulting company focused on business development dealing with C-level and one level below we new business cards.
We have decided to use KMR (Kestrel Meridian Rowe) as the business name. The legal name will be Kestrel Meridian Rowe ApS but we will brand us under KMR. The tack line is “Shaping Lasting Gains” if we need one.
For legal reasons we need to have the legal name on the letters together with the company no. (cvr. nr. 58117904)
We want to signal the following:
- Serious
- Professional
- Creating Result
- Capable of thinking out of the box and creative
- Fast reactions we will be there when needed
What we do not want to be view as is:
- To smart
- We know better
- We can fix it yesterday
Our Value Proposition is two sited:
- Increasing revenue
- Reduced sales cost or increased efficiency
Therefore, companies can call us when they want to grow or they need to be more efficient.
Our business cards should have a two sided print with the logo incl. the tack line on one side and the detailed information on the other site.
We need to have the following information on the letter head:
- Legal company name
- Cvr nr.
- Address incl. country name (Denmark)
- Main number
- Wed address
Symbols are welcome to be used to guide for the above information.
The following information are expected to be in the personal signature of the letter.
- Name
- Title
- Mobile number
- E-mail address
Updates
Some of you has requested our specific details so here they come:
- Address incl. country name (Denmark): Lyngvænget 42, 3460 Birkerød, Denmark
- Main number: +45 7081 5532
- Wed address: www.kmrhalo.com
Mobile no. are +45 xxxx xxxx or +45 2287 3104
Our e-mail looks like this: firstname.seconname@KMRHALO.COM or for me: jonas.vallgren@kmrhalo.com
We need the design (file) as finish as posible so we just need to add personal details before printing.
Please be aware that we will prefer designs where we can print the full letter incl. design. As we are communicating on e-mails with pdf versions of the letter we also need to have a design which will print on the clients printers.
Target Market(s)
C level and one level below.
Major local and international Companies.
Industry/Entity Type
Management Consulting
Font styles to use
Colors
Designer to choose colors to be used in the design.
Requirements
Must have
- Use of our logo without tack line

```html
<!DOCTYPE html>
<html lang="en">
<head>
<meta charset="utf-8">
<title>KMR Letterhead</title>
<link rel="stylesheet" href="https://fonts.googleapis.com/css2?family=Arimo:wght@400;700&family=Dancing+Script:wght@700&display=swap">
<style>
  :root {
    --brand-blue: #0a5bb0;
    --brand-deep: #0b4f9e;
    --brand-light: #4aa3e0;
    --ink: #3a3a3a;
    --muted: #555;
    --paper: #ffffff;
    --backdrop: #eeeeee;
  }
  * { margin: 0; padding: 0; box-sizing: border-box; }
  html, body { width: 1200px; height: 1076px; overflow: hidden; }
  body {
    background: var(--backdrop);
    font-family: "Arimo", Arial, sans-serif;
    color: var(--ink);
    position: relative;
  }
  .letterhead {
    position: absolute;
    left: 246px; top: 38px;
    width: 708px; height: 1000px;
    background: var(--paper);
    box-shadow: 0 4px 18px rgba(0,0,0,.12);
    overflow: hidden;
  }
  .band { position: absolute; left: 0; width: 708px; display: block; }
  .band--top { top: 0; height: 90px; }
  .band--bottom { bottom: 0; height: 130px; }

  .company {
    position: absolute; right: 40px; top: 62px; text-align: right;
  }
  .company__name { color: var(--brand-blue); font-weight: 700; font-size: 15px; }
  .company__tagline { color: var(--brand-blue); font-size: 9px; margin-top: 2px; }

  .brand {
    position: absolute; left: 42px; top: 102px;
  }
  .brand__name {
    color: var(--brand-blue); font-weight: 700; font-size: 44px; line-height: 1; letter-spacing: 1px;
  }
  .brand__cvr {
    color: var(--brand-blue); font-weight: 700; font-size: 10px; margin-top: 8px; padding-left: 4px;
  }

  .letter-body {
    position: absolute; left: 50px; right: 48px; top: 196px;
    font-size: 10px; line-height: 1.3; color: var(--muted);
  }
  .letter-body__heading { color: var(--brand-blue); font-weight: 700; font-size: 12px; margin-bottom: 8px; }
  .letter-body p { margin-bottom: 10px; text-align: justify; }

  .sign-off { position: absolute; left: 50px; top: 724px; }
  .sign-off__closing { font-size: 12px; color: var(--muted); }
  .sign-off__signature {
    font-family: "Dancing Script", cursive; font-size: 20px; color: #333; margin: 12px 0 8px;
  }
  .sign-off__name { color: var(--brand-blue); font-weight: 700; font-size: 17px; }
  .sign-off__title, .sign-off__contact { font-size: 9.5px; color: #444; margin-top: 4px; }

  .footer-address {
    position: absolute; left: 0; width: 500px; bottom: 30px; text-align: center;
    color: #fff; font-weight: 700; font-size: 15px; letter-spacing: .3px;
  }
  .footer-web {
    position: absolute; right: 26px; bottom: 62px;
    color: #fff; font-weight: 700; font-size: 13px;
  }
</style>
</head>
<body>
  <main class="letterhead">
    <svg class="band band--top" viewBox="0 0 708 90" preserveAspectRatio="none" aria-hidden="true">
      <defs>
        <linearGradient id="topShade" x1="0" x2="1" y1="0" y2="0">
          <stop offset="0" stop-color="var(--brand-deep)"/>
          <stop offset=".55" stop-color="var(--brand-light)"/>
          <stop offset="1" stop-color="var(--brand-deep)"/>
        </linearGradient>
      </defs>
      <path d="M0 0 H708 V14 Q400 30 0 72 Z" fill="url(#topShade)"/>
      <path d="M0 72 Q400 30 708 14 V20 Q400 40 0 84 Z" fill="#d8e9f7"/>
    </svg>

    <header class="company">
      <div class="company__name">Kestrel Meridian Rowe ApS</div>
      <div class="company__tagline">Shaping Lasting Gains</div>
    </header>

    <div class="brand">
      <div class="brand__name">KMR</div>
      <div class="brand__cvr">CVR. NR. 58117904</div>
    </div>

    <section class="letter-body">
      <h2 class="letter-body__heading">Lorem ipsum</h2>
      <p>Lorem ipsum dolor, consectetuer adipiscing elit, sed diam nonummy nibh euismod tincidunt ut laoreet dolore magna aliquam erat volutpat. Ut wisi enim ad minim veniam, quis nostrud exerci tation ullamcorper suscipit lobortis nisl ut aliquip ex ea commodo consequat. Duis autem vel eum iriure dolor in hendrerit in vulputate velit esse molestie consequat, vel illum dolore eu feugiat nulla facilisis minim</p>
      <p>Lorem ipsum dolor, consectetuer adipiscing elit, sed diam nonummy nibh euismod tincidunt ut laoreet dolore magna aliquam erat volutpat. Ut wisi enim ad minim veniam, quis nostrud exerci tation ullamcorper suscipit lobortis nisl ut aliquip ex ea commodo consequat. Duis autem vel eum iriure dolor in hendrerit in vulputate velit esse molestie consequat, vel illum dolore eu feugiat nulla facilisis minim</p>
      <p>Lorem ipsum dolor, consectetuer adipiscing elit, sed diam nonummy nibh euismod tincidunt ut laoreet dolore magna aliquam erat volutpat. Ut wisi enim ad minim veniam, quis nostrud exerci tation ullamcorper suscipit lobortis nisl ut aliquip ex ea commodo consequat. Duis autem vel eum iriure dolor in hendrerit in vulputate velit esse molestie consequat, vel illum dolore eu feugiat nulla facilisis minim</p>
      <p>Lorem ipsum dolor, consectetuer adipiscing elit, sed diam nonummy nibh euismod tincidunt ut laoreet dolore magna aliquam erat volutpat. Ut wisi enim ad minim veniam, quis nostrud exerci tation ullamcorper suscipit lobortis nisl ut aliquip ex ea commodo consequat. Duis autem vel eum iriure dolor in hendrerit in vulputate velit esse molestie consequat, vel illum dolore eu feugiat nulla facilisis minim</p>
      <p>Lorem ipsum dolor, consectetuer adipiscing elit, sed diam nonummy nibh euismod tincidunt ut laoreet dolore magna aliquam erat volutpat. Ut wisi enim ad minim veniam, quis nostrud exerci tation ullamcorper suscipit lobortis nisl ut aliquip ex ea commodo consequat. Duis autem vel eum iriure dolor in hendrerit in vulputate velit esse molestie consequat, vel illum dolore eu feugiat nulla facilisis minim</p>
      <p>Lorem ipsum dolor, consectetuer adipiscing elit, sed diam nonummy nibh euismod tincidunt ut laoreet dolore magna aliquam erat volutpat. Ut wisi enim ad minim veniam, quis nostrud exerci tation ullamcorper suscipit lobortis nisl ut aliquip ex ea commodo consequat. Duis autem vel eum iriure dolor in hendrerit in vulputate velit esse molestie consequat, vel illum dolore eu feugiat nulla facilisis minim</p>
      <p>Lorem ipsum dolor, consectetuer adipiscing elit, sed diam nonummy nibh euismod tincidunt ut laoreet dolore magna aliquam erat volutpat. Ut wisi enim ad minim veniam, quis nostrud exerci tation ullamcorper suscipit lobortis nisl ut aliquip ex ea commodo consequat. Duis autem vel eum iriure dolor in hendrerit in vulputate velit esse molestie consequat, vel illum dolore eu feugiat nulla facilisis minim</p>
      <p>Lorem ipsum dolor, consectetuer adipiscing elit, sed diam nonummy nibh euismod tincidunt ut laoreet dolore magna aliquam erat volutpat. Ut wisi enim ad minim veniam, quis nostrud exerci tation ullamcorper suscipit lobortis nisl ut</p>
    </section>

    <section class="sign-off">
      <div class="sign-off__closing">Yours Sincerly,</div>
      <div class="sign-off__signature">Yours Signature</div>
      <div class="sign-off__name">Your full name</div>
      <div class="sign-off__title">Monoging Director</div>
      <div class="sign-off__contact">(00) 00-00-00-00</div>
      <div class="sign-off__contact">yourname@yourwebsite.com</div>
    </section>

    <svg class="band band--bottom" viewBox="0 0 708 130" preserveAspectRatio="none" aria-hidden="true">
      <defs>
        <linearGradient id="footShade" x1="0" x2="1" y1="0" y2="0">
          <stop offset="0" stop-color="var(--brand-deep)"/>
          <stop offset=".5" stop-color="var(--brand-light)"/>
          <stop offset="1" stop-color="var(--brand-deep)"/>
        </linearGradient>
      </defs>
      <path d="M0 130 V82 Q300 70 708 0 V130 Z" fill="url(#footShade)"/>
      <path d="M0 82 Q300 70 708 0 V-4 Q300 64 0 76 Z" fill="#d8e9f7"/>
      <path d="M498 130 L526 50 L532 48 L504 130 Z" fill="#ffffff"/>
    </svg>

    <div class="footer-address">Your Address, Street No., Denmark</div>
    <div class="footer-web">www.yourwebsite.com</div>
  </main>
</body>
</html>
```